Business cards to launch an education platform

Hi,
I am looking at having new business cards designed.
I am a startup, developing a web platform for schools and university, the education world. It's an online assessment system.
I would like a card that looks classy, and that is using the colors and the font of my logo.

I have attached:
1) my logo
2) A business card that I have designed quickly so you can have all the information required in the card, but I really don't like it.
3) The font that I am using (Lato Regular) to design my web platform
4) Some screenshots of my web platform so you can have a look at the style that I have.

Target Market(s)

Major market: Education system: Schools and university
Minor markets: Business in general

Industry/Entity Type

Business

Contact Information for Business Card

Clara Fenwick
Director

M: 0437 518 902
E: clara.fenwick@amberLoomSystems.com.au

Requirements
Must have
• The colors of my logo

```html
<!DOCTYPE html>
<html lang="en">
<head>
<meta charset="utf-8">
<title>Amber Loom Systems – Business Cards</title>
<link rel="stylesheet" href="https://fonts.googleapis.com/css2?family=Arimo:wght@400;700&family=Lato:wght@400&display=swap">
<style>
  :root {
    --page-bg: #e9e7e3;
    --card-white: #fbfbfb;
    --card-black: #0b0b0c;
    --brand-blue: #1d6fb3;
    --brand-cyan: #2cb4e3;
    --name-blue: #1565ad;
    --ink: #1f1f1f;
    --rule: #2a2a2a;
    --icon-blue: #2f7fc0;
  }
  * { margin: 0; padding: 0; box-sizing: border-box; }
  html, body {
    width: 1200px; height: 892px; overflow: hidden;
    background: var(--page-bg);
  }
  .canvas {
    position: relative; width: 1200px; height: 892px;
    display: flex; flex-direction: column; align-items: center; justify-content: center; gap: 56px;
  }
  .card {
    position: relative; width: 560px; height: 320px; border-radius: 22px;
    box-shadow: 0 10px 28px rgba(0,0,0,0.18);
    overflow: hidden;
  }
  .card--front { background: var(--card-white); }
  .card--back { background: var(--card-black); display: flex; align-items: center; justify-content: center; }

  .brand {
    display: flex; align-items: center; gap: 14px;
    font-family: "Lato", sans-serif; font-weight: 400; color: var(--brand-blue);
  }
  .brand__mark { width: 22px; height: 22px; background: var(--brand-blue); flex: none; }
  .brand__name { font-size: 26px; letter-spacing: 0.05em; white-space: nowrap; line-height: 1; }
  .card--front .brand { position: absolute; left: 34px; top: 46px; }
  .card--back .brand { color: var(--brand-cyan); }
  .card--back .brand__mark { background: var(--brand-cyan); width: 26px; height: 26px; }
  .card--back .brand__name { font-size: 32px; }

  .person {
    position: absolute; right: 24px; top: 106px; text-align: right;
    font-family: "Arimo", sans-serif; white-space: nowrap;
  }
  .person__name { font-size: 30px; font-weight: 700; color: var(--name-blue); letter-spacing: -0.01em; line-height: 36px; }
  .person__role { font-size: 16px; color: var(--ink); line-height: 20px; margin-top: 4px; }

  .divider { position: absolute; left: 0; width: 346px; top: 146px; height: 1.5px; background: var(--rule); }

  .contact {
    position: absolute; left: 80px; bottom: 30px;
    font-family: "Arimo", sans-serif; font-size: 16px; color: var(--ink); white-space: nowrap;
  }
  .contact__row { display: flex; align-items: center; gap: 10px; line-height: 26px; }
  .contact__icon { width: 16px; height: 16px; flex: none; }
</style>
</head>
<body>
<main class="canvas">
  <section class="card card--front" aria-label="Business card front">
    <div class="brand">
      <span class="brand__mark"></span>
      <span class="brand__name">Amber Loom Systems</span>
    </div>
    <div class="person">
      <p class="person__name">Clara Fenwick</p>
      <p class="person__role">Director</p>
    </div>
    <div class="divider"></div>
    <div class="contact">
      <p class="contact__row">
        <svg class="contact__icon" viewBox="0 0 16 16" aria-hidden="true">
          <rect width="16" height="16" rx="2" fill="var(--icon-blue)"/>
          <path d="M5 3.5 L6.8 5.6 L5.9 6.7 Q7 9 9.3 10.1 L10.4 9.2 L12.5 11 L11.4 12.5 Q6 12 3.5 4.6 Z" fill="#fff"/>
        </svg>
        <span>0437 518 902</span>
      </p>
      <p class="contact__row">
        <svg class="contact__icon" viewBox="0 0 16 16" aria-hidden="true">
          <rect width="16" height="16" rx="2" fill="var(--icon-blue)"/>
          <rect x="3" y="4.5" width="10" height="7" fill="none" stroke="#fff" stroke-width="1.2"/>
          <path d="M3 4.5 L8 8.6 L13 4.5" fill="none" stroke="#fff" stroke-width="1.2"/>
        </svg>
        <span>clara.fenwick@amberLoomSystems.com.au</span>
      </p>
    </div>
  </section>

  <section class="card card--back" aria-label="Business card back">
    <div class="brand">
      <span class="brand__mark"></span>
      <span class="brand__name">Amber Loom Systems</span>
    </div>
  </section>
</main>
</body>
</html>
```